Mobile Disc Jockey Service Brochure

We are looking for a brochure to showcase our Mobile DJ Business. It needs to be something professional looking and fit our target market of Weddings. We cater to events of all types but majority of our clients are brides looking for professional service at affordable prices.

Our website for reference: http://www.theclefcart.com/
facebook for reference: https://www.facebook.com/MarcusClefCart

I've uploaded a picture of us, our logo and some other photos that might be useful. Feel free to use additional stock photos that may be applicable to our project needs. Feel free to crop photos as necessary

I'd like this to be an 8 1/2" x 11" bifold, or trifold brochure, double sided. The front can be simple with our logo and phone number. Back can also be simple with a small logo and our website. I'd like one of the areas to focus on our bio and picture, and the other areas can describe our packages and what we offer as well as our mission statement

Some other information: We provide not only Professional and Enthusiastic DJ Services but we also do Uplighting as well as Event planning.

Target Market(s)

Weddings, Anniversary Parties, Birthdays, Themed Party

Industry/Entity Type

Business

Requirements
Must have
• Something describing our services like the following (feel free to rearrange the wording if necessary).
• All packages are hourly and custom built to fit your party needs. A list of our offerings includes:
• Cocktail music, dinner music, dance music
• Ultimate coordination of activities and unique event planning experience
• HD Sound
• LED Light Show
• Wireless Microphone System
• Unlimited choice of song titles from Digital to Vinyl
• Free travel within 50 miles - Travel outside of this is calculated with a fee per additional mile.
• Optional Services:
• Projector with Screen for Slide Shows & Movies
• Uplighting
• We provide a Fun & Easy to use web interface that walks you through the timeline of your event capturing every detail you desire, making planning fun! We guarantee you will hear everything you want, we have an endless music library as well as mobile internet so we can access any song you and your guests want instantly! In addition to the Online Event Planner, we offer unlimited consultations prior to your event to ensure face to face that you are getting everything you want and more.
• I'd like to see something featuring our services as well as our picture that I uploaded maybe cropped at the chest level or there abouts with this information:
• We are a husband and wife team. Marcus Holloway, the DJ has been providing custom soundtracks for events of all types for well over a decade. In 2011 his wife Tessa joined the team to handle all of the event coordination and logistics. Together we run the Clef Cart offering Professional DJ Services at a personal level. We enjoy working with clients to create the event that they deserve at an affordable price. Contact us today for your quote or visit us online.
• (555) 314-2286
• theclefcart@mailvo.com
• www.theclefcart.com
• www.facebook.com/MarcusClefCart
• Id also like something along the lines of:
• Your choice of DJ can make or break your event. The Clef Cart guarantees to go above and beyond to make your event flawless and unforgettable. We promise to provide nothing but the best, well within your budget. When it comes to Weddings, we recognize that your Wedding is the most important day of your life! We will work with you side by side to ensure that it's everything you have dreamed of and more. Let the experience we provide create a beautiful memory that will last a lifetime.
• (Mission Statement)
• Our mission is to provide high quality and affordable mobile DJ services that will fill your event with beautiful lifelong memories.
Nice to have
• Id like to see the picture of the bride and grandfather dancing put in there somewhere.
• Color Scheme should be a mix of greys, black, white, you can add color as needed to match photos/logo, etc.

```html
<!DOCTYPE html>
<html lang="en">
<head>
<meta charset="utf-8">
<title>The Clef Cart – Brochure Spread</title>
<link rel="stylesheet" href="https://fonts.googleapis.com/css2?family=Open+Sans:wght@400;600;700&display=swap">
<style>
  :root {
    --red: #b3120a;
    --paper: #f1f2f2;
    --grey-light: #dde1e2;
    --grey-mid: #c6cdd0;
    --backdrop: #dfe3e3;
    --ink: #3a3a3a;
    --white: #ffffff;
    --gold: #f0a21c;
  }
  * { box-sizing: border-box; margin: 0; padding: 0; }
  html, body { width: 1200px; height: 1000px; overflow: hidden; }
  body {
    background: var(--backdrop);
    font-family: "Open Sans", Arial, sans-serif;
    color: var(--ink);
  }
  .spread {
    position: absolute; left: 160px; top: 190px;
    width: 880px; height: 620px;
    display: flex;
    box-shadow: 0 10px 30px rgba(0,0,0,.18);
  }
  .panel { position: relative; width: 440px; height: 620px; background: var(--paper); overflow: hidden; }
  .panel-shapes { position: absolute; inset: 0; }

  /* Bio panel */
  .bio-heading { position: absolute; left: 30px; top: 96px; color: var(--white); line-height: 1.2; }
  .bio-heading .kicker { display: block; font-size: 10px; letter-spacing: 1px; font-weight: 400; }
  .bio-heading .title { display: block; font-size: 16px; font-weight: 700; letter-spacing: .5px; }
  .bio-text { position: absolute; left: 30px; top: 170px; width: 255px; font-size: 9.2px; line-height: 1.45; }
  .bio-text p + p { margin-top: 7px; }
  .brand-small {
    position: absolute; right: 30px; top: 412px;
    display: flex; align-items: center; gap: 6px;
    font-size: 12px; font-weight: 600; color: var(--ink);
  }
  .brand-dot { width: 11px; height: 11px; border-radius: 50%; background: var(--red); flex: none; }
  .contact { position: absolute; right: 30px; top: 518px; text-align: right; color: var(--white); font-size: 8.5px; line-height: 1.45; }
  .contact .cta { font-size: 10.5px; margin-bottom: 6px; line-height: 1.3; }
  .contact .social { margin-top: 6px; display: flex; justify-content: flex-end; align-items: center; gap: 5px; }
  .contact .social-square { width: 8px; height: 8px; background: var(--white); }

  /* Cover panel */
  .brand-cover {
    position: absolute; left: 0; right: 0; top: 300px;
    display: flex; justify-content: center; align-items: center; gap: 10px;
    font-size: 28px; font-weight: 600; color: var(--ink);
  }
  .brand-cover .brand-dot { width: 18px; height: 18px; }
  .services { position: absolute; right: 24px; top: 506px; display: flex; }
  .service { width: 108px; text-align: center; color: var(--white); font-size: 9.5px; letter-spacing: .5px; }
  .service + .service { border-left: 1px solid rgba(255,255,255,.45); }
  .service-icon { width: 34px; height: 34px; margin: 0 auto 7px; display: block; }
  .tagline { position: absolute; right: 24px; top: 588px; color: var(--white); font-size: 9px; }
</style>
</head>
<body>
<main class="spread">

  <section class="panel panel-bio">
    <svg class="panel-shapes" viewBox="0 0 440 620" aria-hidden="true">
      <polygon points="0,0 440,0 440,72 0,150" fill="var(--red)"/>
      <polygon points="440,78 255,128 440,330" fill="var(--grey-mid)"/>
      <polygon points="0,330 170,300 300,525 0,555" fill="var(--grey-light)"/>
      <polygon points="300,330 440,330 440,490 300,525" fill="var(--grey-light)"/>
      <polygon points="0,548 440,480 440,620 0,620" fill="var(--red)"/>
    </svg>
    <h2 class="bio-heading"><span class="kicker">OUR</span><span class="title">BIODATA</span></h2>
    <div class="bio-text">
      <p>The Clef Cart provides Professional DJ services for metro Detroit and the surrounding areas. From weddings to parties of any kind, we will go above and beyond to provide your event with a memorable soundtrack!</p>
      <p>Planning your big event can be stressful so why not let us use our expertise and help make your event unforgettable! With professional equipment, lighting and a variety of custom packages available we have what you want and need!</p>
      <p>With a large library of songs, we are guaranteed to have everything you and your guests want to hear! Music is our passion and we look forward to sharing that at your next event!</p>
      <p>We are a husband and wife team. Marcus Holloway, the DJ has been providing custom sound tracks for events of all types for well over a decade. In 2011 his wife Tessa joined the team to handle all of the event coordination and logistics. Together we run the Clef Cart offering Professional DJ Services at a personal level. We enjoy working with clients to create the event that they deserve at an affordable price.</p>
    </div>
    <div class="brand-small"><span class="brand-dot"></span>The Clef Cart</div>
    <div class="contact">
      <p class="cta">Contact us today for your<br>quote or visit us online</p>
      <p>P: (555) 314-2286</p>
      <p>E: theclefcart@mailvo.com</p>
      <p>W: www.theclefcart.com</p>
      <p class="social"><span class="social-square"></span>www.facebook.com/MarcusClefCart</p>
    </div>
  </section>

  <section class="panel panel-cover">
    <svg class="panel-shapes" viewBox="0 0 440 620" aria-hidden="true">
      <polygon points="0,0 440,0 440,150 170,210 0,120" fill="var(--red)"/>
      <polygon points="440,150 170,210 440,430" fill="var(--grey-mid)"/>
      <polygon points="0,120 110,300 0,470" fill="var(--grey-light)"/>
      <polygon points="0,470 110,300 200,520 0,545" fill="var(--grey-mid)" opacity=".6"/>
      <polygon points="0,545 440,480 440,620 0,620" fill="var(--red)"/>
    </svg>
    <div class="brand-cover"><span class="brand-dot"></span>The Clef Cart</div>
    <div class="services">
      <div class="service">
        <svg class="service-icon" viewBox="0 0 38 38" role="img" aria-label="DJ at turntables illustration">
          <rect x="2" y="2" width="34" height="34" rx="4" fill="var(--gold)"/>
        </svg>
        DJ SERVICES
      </div>
      <div class="service">
        <svg class="service-icon" viewBox="0 0 38 38" role="img" aria-label="Disco ball">
          <circle cx="19" cy="19" r="17" fill="#1d2a8c"/>
          <circle cx="12" cy="13" r="3" fill="#e8463a"/>
          <circle cx="22" cy="10" r="3" fill="#f5c400"/>
          <circle cx="27" cy="20" r="3" fill="#3cc46a"/>
          <circle cx="16" cy="24" r="3" fill="#38b6e8"/>
          <circle cx="24" cy="29" r="2.5" fill="#f07ab3"/>
        </svg>
        UPLIGHTING
      </div>
      <div class="service">
        <svg class="service-icon" viewBox="0 0 38 38" role="img" aria-label="Calendar">
          <rect x="3" y="6" width="32" height="29" rx="3" fill="#e85a8c"/>
          <rect x="6" y="13" width="26" height="19" fill="var(--white)"/>
          <g fill="#333">
            <rect x="8" y="15" width="4" height="4"/><rect x="14" y="15" width="4" height="4"/><rect x="20" y="15" width="4" height="4"/><rect x="26" y="15" width="4" height="4"/>
            <rect x="8" y="21" width="4" height="4"/><rect x="14" y="21" width="4" height="4"/><rect x="20" y="21" width="4" height="4"/><rect x="26" y="21" width="4" height="4"/>
            <rect x="8" y="27" width="4" height="3"/><rect x="14" y="27" width="4" height="3"/><rect x="20" y="27" width="4" height="3"/>
          </g>
          <rect x="10" y="3" width="3" height="6" fill="#e85a8c"/><rect x="25" y="3" width="3" height="6" fill="#e85a8c"/>
        </svg>
        EVENT PLANNING
      </div>
    </div>
    <p class="tagline">All packages are hourly and custom built to fit your party needs</p>
  </section>

</main>
</body>
</html>
```